you will use Ai to Copy the website Brivanta.com to come up with the basic frame work and it will give you the understanding of how I would like Kelbrava.com to be like. Kelbrava.com is a peer to peer rv rental site very similar to both of the other rv rental sites the difference is that are commission based 20% and above per rental and we will be one flat monthly rate and they keep all the earnings. Below is photo that will help you with the color scheme and the look and feel of the design

1 page

```html
<!DOCTYPE html>
<html lang="en">
<head>
<meta charset="utf-8">
<title>Kelbrava.com — The smart way to rent an RV</title>
<link href="https://fonts.googleapis.com/css2?family=Plus+Jakarta+Sans:wght@400;500;600;700;800&display=swap" rel="stylesheet">
<style>
:root{
  --navy:#0e1c36;
  --navy-2:#13284a;
  --green:#6dbf2f;
  --green-dark:#2f9a2c;
  --ink:#16202e;
  --muted:#5b6573;
  --line:#e3e7ec;
  --soft:#f5f7fa;
  --white:#ffffff;
}
*{box-sizing:border-box;margin:0;padding:0}
html,body{width:1200px;height:3375px;overflow:hidden}
body{font-family:"Plus Jakarta Sans",Arial,sans-serif;color:var(--ink);background:var(--white);position:relative}
.section{position:absolute;left:0;width:1200px}

/* header */
.site-header{top:0;height:88px;background:var(--navy);display:flex;align-items:center;padding:0 46px}
.brand{color:var(--white);font-weight:800;font-size:30px;letter-spacing:-.5px;display:flex;align-items:center;gap:10px}
.brand-dot{width:14px;height:14px;border-radius:50%;background:var(--green)}
.main-nav{margin-left:auto;display:flex;align-items:center;gap:30px;font-size:15px;font-weight:600;color:var(--white)}
.main-nav span.caret::after{content:" ⌄";font-size:11px;opacity:.8}
.btn{display:inline-flex;align-items:center;justify-content:center;border-radius:5px;font-weight:700;font-size:14px}
.btn-green{background:var(--green);color:var(--white)}
.btn-dark-green{background:var(--green-dark);color:var(--white)}
.signup{width:82px;height:40px}

/* hero */
.hero{top:88px;height:525px;background:linear-gradient(90deg,#0f2236 0%,#1e3a48 40%,#3c5a55 65%,#5b6b58 100%)}
.hero-photo{position:absolute;inset:0;background:radial-gradient(ellipse at 78% 40%,rgba(150,160,150,.35),transparent 55%),linear-gradient(180deg,rgba(120,150,170,.25),rgba(10,25,40,.2) 60%,rgba(20,40,45,.5))}
.hero h1{position:absolute;left:47px;top:120px;font-size:60px;line-height:72px;font-weight:800;color:var(--white);letter-spacing:-1px}
.hero h1 em{font-style:normal;color:var(--green)}
.hero p{position:absolute;left:47px;top:285px;font-size:16px;line-height:27px;color:var(--white)}
.search-box{position:absolute;left:46px;top:385px;width:1015px;height:105px;background:var(--white);border-radius:8px;display:flex;align-items:center;padding:0 30px;gap:30px;box-shadow:0 10px 30px rgba(0,0,0,.2)}
.field{width:175px;border-bottom:1px solid var(--line);padding-bottom:8px}
.field label{display:block;font-size:13px;color:var(--muted);margin-bottom:10px}
.field span{font-size:13px;color:#8a93a0}
.search-btn{margin-left:auto;width:90px;height:48px;font-size:14px}

/* features */
.features{top:613px;height:127px;background:var(--white);display:flex;align-items:center;padding:0 62px;gap:0}
.feature{display:flex;align-items:flex-start;gap:18px;width:270px}
.feature svg{flex:none;margin-top:2px}
.feature b{display:block;font-size:13px;font-weight:700;margin-bottom:8px}
.feature small{font-size:12px;color:var(--muted)}

/* rv types */
.rv-types{top:740px;height:435px;background:var(--soft)}
.rv-types h2{position:absolute;left:44px;top:52px;font-size:27px;font-weight:700}
.rv-types .sub{position:absolute;left:44px;top:105px;font-size:14px;color:var(--muted)}
.outline-btn{border:1.5px solid #9aa3ad;border-radius:5px;background:var(--white);font-size:12px;font-weight:600;color:var(--ink);display:flex;align-items:center;justify-content:center}
.browse{position:absolute;left:1040px;top:86px;width:111px;height:36px}
.type-grid{position:absolute;left:42px;top:161px;display:flex;gap:18px}
.type-card{width:205px;height:226px;background:var(--white);border:1px solid var(--line);border-radius:8px;padding:14px 14px}
.type-card .shot{height:112px;border-radius:4px;background:linear-gradient(180deg,#f7f7f7,#e8eaed)}
.type-card b{display:block;margin-top:44px;font-size:13px;font-weight:700}
.type-card small{display:block;margin-top:10px;font-size:12px;color:var(--muted)}

/* why */
.why{top:1175px;height:528px;background:var(--white)}
.why .eyebrow{position:absolute;left:58px;top:55px;font-size:13px;font-weight:700;color:var(--green-dark);letter-spacing:.4px}
.why h2{position:absolute;left:58px;top:85px;font-size:40px;line-height:48px;font-weight:700;letter-spacing:-.5px}
.why .lead{position:absolute;left:58px;top:197px;font-size:14px;line-height:25px;color:#2c3440}
.checks{position:absolute;left:58px;top:268px;list-style:none}
.checks li{display:flex;align-items:center;gap:12px;font-size:14px;height:37px;color:#2c3440}
.checks li b{font-weight:700}
.why .cta{position:absolute;left:58px;top:428px;width:149px;height:48px}
.why-photo{position:absolute;left:544px;top:0;width:656px;height:528px;background:linear-gradient(180deg,#d6e1ea 0%,#b9c9d6 35%,#6f8a80 55%,#7a6f5a 75%,#4f5550 100%)}

/* how it works */
.how{top:1703px;height:341px;background:var(--soft);text-align:center}
.how h2{position:absolute;left:0;right:0;top:62px;font-size:27px;font-weight:700}
.how .sub{position:absolute;left:0;right:0;top:102px;font-size:14px;color:#2c3440}
.steps{position:absolute;left:143px;top:135px;display:flex;gap:0}
.step{width:238px;display:flex;flex-direction:column;align-items:center}
.step .dot{width:56px;height:56px;border-radius:50%;background:#e4f1da;display:flex;align-items:center;justify-content:center}
.step .num{margin-top:16px;font-size:12px;color:var(--green-dark)}
.step b{margin-top:13px;font-size:14px;font-weight:700}
.step small{margin-top:8px;font-size:12px;line-height:18px;color:var(--muted);width:120px}

/* destinations */
.destinations{top:2044px;height:445px;background:var(--white);text-align:center}
.destinations h2{position:absolute;left:0;right:0;top:36px;font-size:27px;font-weight:700}
.destinations .sub{position:absolute;left:0;right:0;top:76px;font-size:14px;color:#2c3440}
.dest-grid{position:absolute;left:42px;top:114px;display:flex;gap:15px}
.dest-card{position:relative;width:262px;height:243px;border-radius:8px;overflow:hidden;text-align:left}
.dest-card::after{content:"";position:absolute;inset:0;background:linear-gradient(180deg,transparent 50%,rgba(0,0,0,.55))}
.dest-card .label{position:absolute;left:15px;bottom:14px;z-index:1;color:var(--white)}
.dest-card b{display:block;font-size:17px;font-weight:700}
.dest-card small{display:block;margin-top:5px;font-size:13px}
.canyon{background:linear-gradient(160deg,#9db4c8 0%,#b5704a 35%,#8a3f26 70%,#5a2e1e 100%)}
.tahoe{background:linear-gradient(180deg,#a4b8c9 0%,#4e6b6a 40%,#2c5a82 70%,#27456a 100%)}
.yellowstone{background:linear-gradient(180deg,#c7c3a6 0%,#6c7a4c 40%,#8a6a42 70%,#4c3c2a 100%)}
.orlando{background:linear-gradient(180deg,#6f9fd0 0%,#9fbfe0 40%,#5e7d8e 70%,#2e4e6a 100%)}
.explore{position:absolute;left:456px;top:393px;width:265px;height:42px}

/* testimonials */
.reviews{top:2489px;height:360px;background:var(--soft);text-align:center}
.reviews h2{position:absolute;left:0;right:0;top:36px;font-size:29px;font-weight:700}
.reviews .sub{position:absolute;left:0;right:0;top:80px;font-size:14px;color:#2c3440}
.review-grid{position:absolute;left:60px;top:115px;display:flex;gap:28px}
.review{width:337px;height:206px;background:var(--white);border:1px solid var(--line);border-radius:6px;padding:20px 22px;text-align:left}
.stars{color:#f2b01e;font-size:14px;letter-spacing:3px}
.review q{display:block;margin-top:18px;font-size:13px;font-weight:600;quotes:"\201C" "\201D"}
.review p{margin-top:14px;font-size:13px;line-height:19px;color:var(--muted);width:220px}
.reviewer{display:flex;align-items:center;gap:14px;margin-top:18px}
.avatar{width:42px;height:42px;border-radius:50%;background:linear-gradient(135deg,#c9b29a,#6b5444)}
.reviewer b{display:block;font-size:13px;font-weight:700}
.reviewer small{font-size:11px;color:var(--muted)}

/* cta band */
.cta-band{top:2849px;height:269px;background:linear-gradient(180deg,#3c4a5e 0%,#26384a 45%,#1d3229 75%,#142419 100%);text-align:center;color:var(--white)}
.cta-band h2{position:absolute;left:0;right:0;top:82px;font-size:36px;font-weight:700}
.cta-band p{position:absolute;left:0;right:0;top:132px;font-size:17px}
.cta-actions{position:absolute;left:413px;top:173px;display:flex;gap:23px}
.cta-actions .btn{width:158px;height:48px}
.btn-ghost{border:1.5px solid var(--white);color:var(--white)}

/* footer */
.site-footer{top:3118px;height:257px;background:var(--navy);color:var(--white)}
.site-footer .brand{position:absolute;left:44px;top:40px}
.footer-about{position:absolute;left:44px;top:90px;font-size:13px;line-height:24px;color:#d5dbe4}
.socials{position:absolute;left:46px;top:174px;display:flex;gap:20px}
.socials span{width:18px;height:18px;border-radius:50%;background:var(--white);display:block}
.footer-col{position:absolute;top:38px}
.footer-col h4{font-size:13px;font-weight:700;letter-spacing:.4px;margin-bottom:16px}
.footer-col a{display:block;font-size:13px;color:#d5dbe4;text-decoration:none;height:30px}
.copyright{position:absolute;left:0;right:0;top:226px;text-align:center;font-size:16px;color:#d5dbe4}
</style>
</head>
<body>

<header class="section site-header">
  <div class="brand"><span class="brand-dot"></span>Kelbrava.com</div>
  <nav class="main-nav">
    <span class="caret">Find an RV</span>
    <span class="caret">List Your RV</span>
    <span class="caret">How It Works</span>
    <span class="caret">Explore</span>
    <span class="caret">Help</span>
    <span>Log In</span>
    <span class="btn btn-green signup">Sign Up</span>
  </nav>
</header>

<section class="section hero">
  <div class="hero-photo" role="img" aria-label="Motorhome parked beside a mountain lake with pine forest and snowy peaks"></div>
  <h1>The smart way<br>to <em>rent an RV.</em></h1>
  <p>Find the perfect RV for your next adventure.<br>From weekend getaways to cross-country road trips.</p>
  <form class="search-box">
    <div class="field"><label>Pick up location</label><span>City, State or Airport</span></div>
    <div class="field"><label>Pick up</label><span>Add dates</span></div>
    <div class="field"><label>Drop off</label><span>Add dates</span></div>
    <div class="field"><label>Guests</label><span>Any</span></div>
    <span class="btn btn-green search-btn">Search</span>
  </form>
</section>

<section class="section features">
  <div class="feature">
    <svg width="30" height="26" viewBox="0 0 30 26" fill="none" stroke="#16202e" stroke-width="2"><rect x="2" y="5" width="22" height="13" rx="2"/><path d="M24 9h3l2 4v5h-5"/><circle cx="8" cy="20" r="3" fill="#fff"/><circle cx="21" cy="20" r="3" fill="#fff"/></svg>
    <div><b>The best selection</b><small>Thousands of RVs nationwide</small></div>
  </div>
  <div class="feature">
    <svg width="28" height="26" viewBox="0 0 28 26" fill="none" stroke="#16202e" stroke-width="2"><path d="M14 3L26 23H2z"/><path d="M14 10v6M14 19v1"/></svg>
    <div><b>24/7 roadside assistance</b><small>Travel with peace of mind</small></div>
  </div>
  <div class="feature">
    <svg width="26" height="28" viewBox="0 0 26 28" fill="none" stroke="#16202e" stroke-width="2"><path d="M13 2l9 4v8c0 6-4 10-9 12-5-2-9-6-9-12V6z"/><path d="M9 14l3 3 5-6"/></svg>
    <div><b>Safe and secure</b><small>Transactions &amp; insurance</small></div>
  </div>
  <div class="feature">
    <svg width="26" height="28" viewBox="0 0 26 28" fill="none" stroke="#16202e" stroke-width="2"><path d="M13 2l9 4v8c0 6-4 10-9 12-5-2-9-6-9-12V6z"/><path d="M13 9l1.8 3.6 3.8.5-2.8 2.6.7 3.8L13 17.7l-3.5 1.8.7-3.8-2.8-2.6 3.8-.5z"/></svg>
    <div><b>Real reviews</b><small>From real renters like you</small></div>
  </div>
</section>

<section class="section rv-types">
  <h2>Find your perfect RV</h2>
  <p class="sub">Explore thousands of RVs from local owners across the country.</p>
  <span class="outline-btn browse">Browse all RVs</span>
  <div class="type-grid">
    <div class="type-card"><div class="shot" role="img" aria-label="Class C drivable motorhome"></div><b>Drivable RVs</b><small>Drive anywhere</small></div>
    <div class="type-card"><div class="shot" role="img" aria-label="Travel trailer"></div><b>Towable RVs</b><small>Easy to tow</small></div>
    <div class="type-card"><div class="shot" role="img" aria-label="Luxury motorhome"></div><b>Luxury RVs</b><small>Premium comfort</small></div>
    <div class="type-card"><div class="shot" role="img" aria-label="Navy camper van"></div><b>Van Conversions</b><small>Adventure ready</small></div>
    <div class="type-card"><div class="shot" role="img" aria-label="Toy hauler trailer with open ramp"></div><b>Toy Haulers</b><small>Bring your toys</small></div>
  </div>
</section>

<section class="section why">
  <p class="eyebrow">WHY RENT ON KELBRAVA.COM?</p>
  <h2>More adventure.<br>Less cost.</h2>
  <p class="lead">Kelbrava.com is a peer-to-peer RV rental marketplace.<br>We make it easy, safe, and affordable to hit the road.</p>
  <ul class="checks">
    <li><svg width="14" height="12" viewBox="0 0 14 12" fill="none" stroke="#2f9a2c" stroke-width="2.2"><path d="M1 6l4 4 8-9"/></svg><span>Save money with one flat monthly rate</span></li>
    <li><svg width="14" height="12" viewBox="0 0 14 12" fill="none" stroke="#2f9a2c" stroke-width="2.2"><path d="M1 6l4 4 8-9"/></svg><span>Keep <b>100%</b> of your earnings</span></li>
    <li><svg width="14" height="12" viewBox="0 0 14 12" fill="none" stroke="#2f9a2c" stroke-width="2.2"><path d="M1 6l4 4 8-9"/></svg><span>20% and above per rental on other platforms</span></li>
    <li><svg width="14" height="12" viewBox="0 0 14 12" fill="none" stroke="#2f9a2c" stroke-width="2.2"><path d="M1 6l4 4 8-9"/></svg><span>List for free. Cancel anytime.</span></li>
  </ul>
  <span class="btn btn-dark-green cta">List Your RV</span>
  <div class="why-photo" role="img" aria-label="Travel trailer driving along a coastal cliff road by the ocean"></div>
</section>

<section class="section how">
  <h2>How it works</h2>
  <p class="sub">Renting an RV has never been easier.</p>
  <div class="steps">
    <div class="step"><div class="dot"><svg width="20" height="20" viewBox="0 0 20 20" fill="none" stroke="#4aa53a" stroke-width="1.8"><rect x="3" y="3" width="14" height="14" rx="2"/><path d="M7 10l2 2 4-4"/></svg></div><span class="num">Step 1</span><b>Find an RV</b><small>Search and filter the perfect RV.</small></div>
    <div class="step"><div class="dot"><svg width="20" height="20" viewBox="0 0 20 20" fill="none" stroke="#4aa53a" stroke-width="1.8"><rect x="3" y="4" width="14" height="13" rx="2"/><path d="M3 8h14M7 2v4M13 2v4"/></svg></div><span class="num">Step 2</span><b>Book &amp; pay</b><small>Secure your booking online.</small></div>
    <div class="step"><div class="dot"><svg width="22" height="20" viewBox="0 0 22 20" fill="none" stroke="#4aa53a" stroke-width="1.8"><rect x="4" y="4" width="14" height="9" rx="2"/><circle cx="7" cy="15" r="2"/><circle cx="15" cy="15" r="2"/></svg></div><span class="num">Step 3</span><b>Hit the road</b><small>Pick up and start your adventure.</small></div>
    <div class="step"><div class="dot"><svg width="20" height="20" viewBox="0 0 20 20" fill="none" stroke="#4aa53a" stroke-width="1.8"><circle cx="10" cy="10" r="7"/><path d="M7 11c1 2 5 2 6 0"/></svg></div><span class="num">Step 4</span><b>Create memories</b><small>Return and share your experience.</small></div>
  </div>
</section>

<section class="section destinations">
  <h2>Popular destinations</h2>
  <p class="sub">Get inspired for your next RV adventure.</p>
  <div class="dest-grid">
    <div class="dest-card canyon" role="img" aria-label="Red rock canyon with a winding river"><div class="label"><b>Grand Canyon, AZ</b><small>1,234 RVs</small></div></div>
    <div class="dest-card tahoe" role="img" aria-label="Pine trees above a blue mountain lake"><div class="label"><b>Lake Tahoe, CA</b><small>823 RVs</small></div></div>
    <div class="dest-card yellowstone" role="img" aria-label="Forest trail at sunset"><div class="label"><b>Yellowstone, WY</b><small>1,076 RVs</small></div></div>
    <div class="dest-card orlando" role="img" aria-label="City skyline beside a lake"><div class="label"><b>Orlando, FL</b><small>912 RVs</small></div></div>
  </div>
  <span class="outline-btn explore">Explore more destinations</span>
</section>

<section class="section reviews">
  <h2>What renters are saying</h2>
  <p class="sub">Real stories from real adventurers.</p>
  <div class="review-grid">
    <article class="review"><div class="stars">★★★★★</div><q>Great RV, great owner, great trip!</q><p>The whole experience was seamless. Highly recommend!</p><div class="reviewer"><span class="avatar" role="img" aria-label="Reviewer portrait"></span><div><b>Nora P.</b><small>Los Angeles, CA</small></div></div></article>
    <article class="review"><div class="stars">★★★★★</div><q>Perfect for our family vacation.</q><p>The RV was clean, comfortable, and exactly as described.</p><div class="reviewer"><span class="avatar" role="img" aria-label="Reviewer portrait"></span><div><b>Marcus D.</b><small>Nashville, TN</small></div></div></article>
    <article class="review"><div class="stars">★★★★★</div><q>We'll definitely rent again!</q><p>Amazing customer service and a smooth pickup.</p><div class="reviewer"><span class="avatar" role="img" aria-label="Reviewer portrait"></span><div><b>Lena K.</b><small>Austin, TX</small></div></div></article>
  </div>
</section>

<section class="section cta-band" role="img" aria-label="Forested mountain valley at dusk">
  <h2>Ready for your next adventure?</h2>
  <p>Join thousands of happy renters and hit the road.</p>
  <div class="cta-actions">
    <span class="btn btn-green">Find an RV</span>
    <span class="btn btn-ghost">List Your RV</span>
  </div>
</section>

<footer class="section site-footer">
  <div class="brand"><span class="brand-dot"></span>Kelbrava.com</div>
  <p class="footer-about">The smart way to rent and share RVs.<br>Peer-to-peer rentals. More adventure.<br>Less cost.</p>
  <div class="socials"><span></span><span></span><span></span></div>
  <div class="footer-col" style="left:389px"><h4>COMPANY</h4><a>About Us</a><a>How It Works</a><a>Careers</a><a>Press</a></div>
  <div class="footer-col" style="left:574px"><h4>SUPPORT</h4><a>Help Center</a><a>Roadside Assistance</a><a>Safety</a><a>Cancellation Policy</a></div>
  <div class="footer-col" style="left:776px"><h4>FOR OWNERS</h4><a>List Your RV</a><a>Owner Resources</a><a>Pricing</a></div>
  <div class="footer-col" style="left:978px"><h4>LEGAL</h4><a>Terms of Service</a><a>Privacy Policy</a><a>Cookie Policy</a></div>
  <p class="copyright">© 2026 kelbrava.com, All rights reserved.</p>
</footer>

</body>
</html>
```